App Design - Career Prep Pal

We require an App Design for our new App called 'Hiring Helper'. This app is essentially an assistant to help Users prepare for job interviews, to help them get hired. <br/><br/>Users who download the App can view common Questions and Answers, save their favourite responses and also view common Interview Tips. <br/><br/>The vision for our App is for Users who are preparing for an interview (1 week before, 1 day before, even 1 hour before), are able to download, view and educate themselves on common questions and responses, and then be confident to land the job. <br/><br/>Our team has developed wireframes to help highlight what each screen should do and include. Please see attached document, which also highlights key requirements for the experience. Feel free to add/remove/edit what you see on these wireframes. Our preference is that you use Adobe XD please.<br/><br/>In terms of design guidelines, we want the experience to be simple, intuitive and 'memorable' to help Users to remember the questions/responses when they are in the interview. <br/><br/>The final design should communicate 'neat and clean professionalism'; we like the design of: jobvista net au<br/><br/>Thank you for reading! Good luck !

Target Market(s)

Professional job seekers

Font styles to use
Sans Serif

Colors

Designer to choose colors to be used in the design.

Requirements
Must have
• Please see my PixelGuild_UX file that I have uploaded
Nice to have
• Could you also please include some ideas on how we can incorporate Advertising into the app screens

```html
<!DOCTYPE html>
<html lang="en">
<head>
<meta charset="utf-8">
<title>Hiring Helper – App Screens</title>
<link href="https://fonts.googleapis.com/css2?family=Montserrat:wght@600&family=Open+Sans:wght@400;600&display=swap" rel="stylesheet">
<style>
:root{
  --bg:#ffffff;
  --blue:#2f6bf0;
  --blue-hero-a:#3554c9;
  --blue-hero-b:#3b7cf5;
  --text:#4a4a55;
  --muted:#8a8d99;
  --line:#e6e9f2;
  --card-shadow:0 1px 4px rgba(40,60,140,.14);
  --nav-icon:#b9bcc6;
  --nav-active:#1d1d26;
  --green:#5bbd4e;
  --orange:#f4a21b;
  --ink-dark:#1f2230;
}
*{box-sizing:border-box;margin:0;padding:0}
html,body{width:822px;height:1200px;overflow:hidden;background:var(--bg)}
body{font-family:"Open Sans",Arial,sans-serif;color:var(--text);position:relative}
.board{position:absolute;left:22px;top:36px;display:grid;grid-template-columns:repeat(4,178px);grid-template-rows:repeat(3,356px);column-gap:22px;row-gap:24px}
.screen{position:relative;width:178px;height:356px;border-radius:18px;overflow:hidden;background:#fff;box-shadow:0 6px 18px rgba(70,90,200,.18)}
.hero{position:absolute;left:0;top:0;width:100%;height:72px;background:linear-gradient(135deg,var(--blue-hero-a),var(--blue-hero-b))}
.brand{position:absolute;top:22px;width:100%;text-align:center;color:#fff;font-family:"Montserrat",Arial,sans-serif;font-weight:600;font-size:11px;letter-spacing:.2px}
.panel{position:absolute;left:0;right:0;top:60px;bottom:30px;background:#fff;border-radius:8px 8px 0 0;padding:10px 8px;overflow:hidden}
.nav{position:absolute;left:0;right:0;bottom:0;height:30px;display:flex;justify-content:space-around;align-items:center;background:#fff;border-top:1px solid #f1f2f6}
.nav svg{width:10px;height:10px;fill:var(--nav-icon)}
.nav svg.on{fill:var(--nav-active)}
.title{color:var(--blue);font-weight:600;font-size:8.5px;text-align:center}
.sub{font-size:7px;text-align:center;margin-top:6px;color:var(--text)}
.back{display:inline-flex;width:11px;height:11px;border-radius:50%;border:1px solid var(--line);align-items:center;justify-content:center;color:var(--blue);font-size:7px;vertical-align:middle;margin-right:5px}
.bar-btn{position:relative;background:#fff;box-shadow:var(--card-shadow);border-left:3px solid var(--blue);height:26px;margin:9px 2px 0;display:flex;align-items:center;justify-content:center;font-size:7px}
.cta{display:block;margin:14px auto 0;width:54px;height:17px;line-height:17px;text-align:center;background:var(--blue);color:#fff;font-size:7px;border-radius:2px}
.art{border-radius:6px}
.q-card{position:relative;box-shadow:var(--card-shadow);border-left:3px solid var(--blue);padding:6px 22px 6px 8px;font-size:5.8px;line-height:1.6;margin-top:6px}
.qmark{position:absolute;right:6px;top:6px;width:12px;height:12px;border-radius:50%;border:1px solid var(--blue);color:var(--blue);font-size:7px;font-weight:600;display:flex;align-items:center;justify-content:center}
.q-head{position:relative;box-shadow:var(--card-shadow);padding:7px 22px 7px 10px;font-size:6px;line-height:1.6;margin:0 4px}
.q-head.center{text-align:center}
.arrow{position:absolute;top:50%;margin-top:-4px;width:8px;height:8px;border-radius:50%;border:1px solid var(--line);background:#fff;font-size:5px;color:var(--muted);display:flex;align-items:center;justify-content:center}
.arrow.l{left:-5px}.arrow.r{right:-5px}
.resp{position:relative;box-shadow:var(--card-shadow);border-left:3px solid var(--blue);margin-top:9px;font-size:5.8px;line-height:1.6}
.resp-top{background:#eef3ff;color:var(--blue);font-size:7px;padding:2px 6px}
.resp p{padding:3px 6px 4px}
.heart{position:absolute;right:5px;top:2px;width:11px;height:11px;border-radius:50%;border:1px solid var(--blue);display:flex;align-items:center;justify-content:center}
.heart svg{width:6px;height:6px;fill:none;stroke:var(--blue);stroke-width:1.4}
.heart.fav svg{fill:var(--blue)}
.saved{position:relative;box-shadow:var(--card-shadow);margin-top:8px;font-size:5.8px;line-height:1.6}
.saved-top{color:var(--blue);font-size:7px;padding:3px 8px;border-bottom:1px solid var(--line)}
.saved p{padding:3px 8px 4px}
.close{position:absolute;right:5px;top:3px;width:10px;height:10px;border-radius:50%;border:1px solid var(--muted);font-size:6px;color:var(--muted);display:flex;align-items:center;justify-content:center}
.tab{color:var(--blue);font-size:7px;margin:8px 0 2px 2px}
.tab-line{width:20px;height:2px;background:var(--blue);margin:0 0 4px 3px}
.tip{position:relative;box-shadow:var(--card-shadow);border-left:3px solid var(--blue);margin-top:7px;height:25px;display:flex;align-items:center;padding-left:18px;font-size:6px;line-height:1.4}
.tip b{position:absolute;left:-3px;top:6px;width:12px;height:12px;border-radius:50%;background:var(--blue);color:#fff;font-size:7px;font-weight:600;display:flex;align-items:center;justify-content:center}
.body-card{box-shadow:var(--card-shadow);border-left:3px solid var(--blue);margin:22px 4px 0;padding:8px;font-size:5.8px;line-height:1.75}
.check{display:block;margin:16px auto 10px;width:18px;height:18px}
.intro{font-size:6.8px;line-height:1.75;text-align:center;padding:0 2px}
.dark .hero{background:linear-gradient(135deg,#26314f,#2d3a63)}
.dark .brand{color:#4b5675}
.shade{position:absolute;inset:0 0 30px 0;background:var(--ink-dark)}
.modal{position:absolute;left:8px;right:8px;top:60px;height:194px;background:#fff}
.modal-top{background:var(--green);height:96px;padding-top:50px;text-align:center;color:#fff}
.modal-top h3{font-size:9px;font-weight:600}
.modal-top p{font-size:5.8px;line-height:1.6;margin-top:2px}
.badge{position:absolute;left:50%;top:-10px;margin-left:-25px;width:50px;height:50px;border-radius:50%;background:#fff;display:flex;align-items:center;justify-content:center;z-index:2}
.badge span{width:36px;height:36px;border-radius:50%;background:linear-gradient(135deg,#f2c94c,#b8860b)}
.modal-body{text-align:center;font-size:6.5px;line-height:1.7;padding:12px 8px 0;color:#6a6d78}
.modal-body em{font-style:normal;color:var(--orange);font-weight:600}
.login{display:block;margin:8px auto 0;width:66px;height:17px;line-height:17px;border-radius:9px;background:var(--orange);color:#fff;font-size:8px;text-align:center}
.modal-x{position:absolute;right:4px;top:56px;width:10px;height:10px;border-radius:50%;background:#fff;border:1px solid #222;font-size:6px;color:#222;display:flex;align-items:center;justify-content:center;z-index:3}
</style>
</head>
<body>
<svg width="0" height="0" style="position:absolute">
  <symbol id="i-home" viewBox="0 0 10 10"><path d="M5 .8 0 5h1.4v4.2h2.6V6.4h2v2.8h2.6V5H10z"/></symbol>
  <symbol id="i-search" viewBox="0 0 10 10"><path d="M4.2 0a4.2 4.2 0 0 1 3.3 6.8L10 9.3 9.3 10 6.8 7.5A4.2 4.2 0 1 1 4.2 0zm0 1.4a2.8 2.8 0 1 0 0 5.6 2.8 2.8 0 0 0 0-5.6z"/></symbol>
  <symbol id="i-add" viewBox="0 0 10 10"><path d="M1.5 0h7A1.5 1.5 0 0 1 10 1.5v7A1.5 1.5 0 0 1 8.5 10h-7A1.5 1.5 0 0 1 0 8.5v-7A1.5 1.5 0 0 1 1.5 0zM4.3 2.5v2H2.3v1.2h2v2h1.4v-2h2V4.5h-2v-2z"/></symbol>
  <symbol id="i-heart" viewBox="0 0 10 10"><path d="M5 9.3.9 5.2A2.6 2.6 0 0 1 5 1.9a2.6 2.6 0 0 1 4.1 3.3z"/></symbol>
  <symbol id="i-user" viewBox="0 0 10 10"><circle cx="5" cy="2.8" r="2.4"/><path d="M0 10c0-3 2.2-4.4 5-4.4S10 7 10 10z"/></symbol>
  <symbol id="i-h" viewBox="0 0 10 10"><path d="M5 9 1 5a2.4 2.4 0 0 1 4-3 2.4 2.4 0 0 1 4 3z"/></symbol>
</svg>

<main class="board">

  <section class="screen">
    <div class="hero"><div class="brand">Hiring Helper</div></div>
    <div class="panel">
      <svg class="check" viewBox="0 0 20 20"><circle cx="10" cy="10" r="8.5" fill="none" stroke="#5bbd4e" stroke-width="1.4"/><path d="M5.5 10.2 8.8 13.3 15.5 5.8" fill="none" stroke="#5bbd4e" stroke-width="1.6" stroke-linecap="round"/></svg>
      <p class="intro">Your Guide to the Most Common Interview Qustions, and the best Resonsws to help you Get hired.</p>
    </div>
    <nav class="nav"><svg class="on"><use href="#i-home"/></svg><svg><use href="#i-search"/></svg><svg><use href="#i-add"/></svg><svg><use href="#i-heart"/></svg><svg><use href="#i-user"/></svg></nav>
  </section>

  <section class="screen">
    <div class="hero"><div class="brand">Hiring Helper</div></div>
    <div class="panel">
      <div class="bar-btn" style="margin-top:24px">View Questions &amp; Responsses</div>
      <div class="bar-btn">My Questions Portfolio</div>
      <div class="bar-btn">Interview Tips</div>
      <div class="art" role="img" aria-label="Illustration of a person working on a laptop beside a video screen" style="width:62px;height:50px;margin:16px auto 0;background:linear-gradient(135deg,#cfe0ff,#4a7ff0)"></div>
    </div>
    <nav class="nav"><svg class="on"><use href="#i-home"/></svg><svg><use href="#i-search"/></svg><svg><use href="#i-add"/></svg><svg><use href="#i-heart"/></svg><svg><use href="#i-user"/></svg></nav>
  </section>

  <section class="screen">
    <div class="hero"><div class="brand">Hiring Helper</div></div>
    <div class="panel">
      <p class="title" style="margin-top:18px">View Questions &amp; Responsses</p>
      <p class="sub">Selection Your Question Category</p>
      <div class="bar-btn" style="margin-top:10px">Behavioural</div>
      <div class="bar-btn">Situational</div>
      <div class="bar-btn">Motivational</div>
      <div class="bar-btn">Technical</div>
      <span class="cta">View All</span>
    </div>
    <nav class="nav"><svg class="on"><use href="#i-home"/></svg><svg><use href="#i-search"/></svg><svg><use href="#i-add"/></svg><svg><use href="#i-heart"/></svg><svg><use href="#i-user"/></svg></nav>
  </section>

  <section class="screen">
    <div class="hero"><div class="brand">Hiring Helper</div></div>
    <div class="panel">
      <p class="title" style="text-align:left;margin-top:16px"><span class="back">‹</span>View Questions &amp; Responsses</p>
      <p class="tab">Behavioural</p><div class="tab-line"></div>
      <div class="q-card">Give me an example of new idea or initiative You have suggested to your manager .How did you implement this idea?<span class="qmark">?</span></div>
      <div class="q-card">Give me an example of a time when you made a mistake or didn't Deliver on expectations, what happened ? what did you learn ?<span class="qmark">?</span></div>
      <div class="q-card">How would your colleagues describe you in three words ?<span class="qmark">?</span></div>
      <div class="q-card">What steps would you take to make an important decision on the job ?<span class="qmark">?</span></div>
    </div>
    <nav class="nav"><svg class="on"><use href="#i-home"/></svg><svg><use href="#i-search"/></svg><svg><use href="#i-add"/></svg><svg><use href="#i-heart"/></svg><svg><use href="#i-user"/></svg></nav>
  </section>

  <section class="screen">
    <div class="hero"><div class="brand">Hiring Helper</div></div>
    <div class="panel">
      <div class="q-head" style="margin-top:6px">Give me an example of new idea or initiative You have suggested to your manager .How did you implement this idea?<span class="qmark">?</span><span class="arrow l">‹</span><span class="arrow r">›</span></div>
      <div class="resp" style="margin-top:14px"><div class="resp-top">Response-1</div><span class="heart fav"><svg viewBox="0 0 10 10"><use href="#i-h"/></svg></span><p>I Was Attracted to this Organisation because of the culture and what I have read on Staffly Reviews I was Very Impressed</p></div>
      <div class="resp"><div class="resp-top">Response-2</div><span class="heart"><svg viewBox="0 0 10 10"><use href="#i-h"/></svg></span><p>I Was Attracted to this Organisation because of the culture and what I have read on Staffly Reviews I was Very Impressed</p></div>
      <div class="resp"><div class="resp-top">Response-3</div><span class="heart"><svg viewBox="0 0 10 10"><use href="#i-h"/></svg></span><p>I Was Attracted to this Organisation because of the culture and what I have read on Staffly Reviews I was Very Impressed</p></div>
    </div>
    <nav class="nav"><svg class="on"><use href="#i-home"/></svg><svg><use href="#i-search"/></svg><svg><use href="#i-add"/></svg><svg><use href="#i-heart"/></svg><svg><use href="#i-user"/></svg></nav>
  </section>

  <section class="screen">
    <div class="hero"><div class="brand">Hiring Helper</div></div>
    <div class="panel">
      <div class="q-head" style="margin-top:6px">Give me an example of a time when you made a mistake or didn't Deliver on expectations, what happened ? what did you learn ?<span class="qmark">?</span><span class="arrow l">‹</span><span class="arrow r">›</span></div>
      <div class="resp" style="margin-top:14px"><div class="resp-top">Response-1</div><span class="heart"><svg viewBox="0 0 10 10"><use href="#i-h"/></svg></span><p>I Was Attracted to this Organisation because of the culture and what I have read on Staffly Reviews I was Very Impressed</p></div>
      <div class="resp"><div class="resp-top">Response-2</div><span class="heart"><svg viewBox="0 0 10 10"><use href="#i-h"/></svg></span><p>I Was Attracted to this Organisation because of the culture and what I have read on Staffly Reviews I was Very Impressed</p></div>
      <div class="resp"><div class="resp-top">Response-3</div><span class="heart fav"><svg viewBox="0 0 10 10"><use href="#i-h"/></svg></span><p>I Was Attracted to this Organisation because of the culture and what I have read on Staffly Reviews I was Very Impressed</p></div>
    </div>
    <nav class="nav"><svg class="on"><use href="#i-home"/></svg><svg><use href="#i-search"/></svg><svg><use href="#i-add"/></svg><svg><use href="#i-heart"/></svg><svg><use href="#i-user"/></svg></nav>
  </section>

  <section class="screen">
    <div class="hero"><div class="brand">Hiring Helper</div></div>
    <div class="panel">
      <p class="title" style="text-align:left;margin:10px 0 0 6px"><span class="back">‹</span>My Question Portfolio</p>
      <p style="font-size:6.3px;line-height:1.6;margin:8px 20px 12px 8px">These are your saved answers that you favourited</p>
      <div class="saved"><div class="saved-top">What are your greatest Strengths</div><span class="close">×</span><p>I Was Attracted to this Organisation because of the culture and what I have read on Staffly Reviews I was Very Impressed</p></div>
      <div class="saved"><div class="saved-top">What do you see yourself in Five</div><span class="close">×</span><p>I Was Attracted to this Organisation because of the culture and what I have read on Staffly Reviews I was Very Impressed</p></div>
      <div class="saved"><div class="saved-top">Why Should We Hire you</div><span class="close">×</span><p>I Was Attracted to this Organisation because of the culture and what I have read</p></div>
    </div>
    <nav class="nav"><svg class="on"><use href="#i-home"/></svg><svg><use href="#i-search"/></svg><svg><use href="#i-add"/></svg><svg><use href="#i-heart"/></svg><svg><use href="#i-user"/></svg></nav>
  </section>

  <section class="screen">
    <div class="hero"><div class="brand">Hiring Helper</div></div>
    <div class="panel">
      <p class="title" style="margin-top:6px">View Questions &amp; Responsses</p>
      <p class="sub">Selection Your Question Category</p>
      <div class="bar-btn" style="margin-top:10px;height:28px">Behavioural</div>
      <div class="bar-btn" style="height:28px">Situational</div>
      <div class="bar-btn" style="height:28px">Motivational</div>
      <div class="bar-btn" style="height:28px">Technical</div>
      <span class="cta" style="margin-top:16px">View All</span>
      <div class="art" role="img" aria-label="Illustration of a person at a desk with a computer" style="position:absolute;right:6px;bottom:2px;width:44px;height:36px;background:linear-gradient(135deg,#dfe8fb,#3a4a7a)"></div>
    </div>
    <nav class="nav"><svg class="on"><use href="#i-home"/></svg><svg><use href="#i-search"/></svg><svg><use href="#i-add"/></svg><svg><use href="#i-heart"/></svg><svg><use href="#i-user"/></svg></nav>
  </section>

  <section class="screen">
    <div class="hero"><div class="brand">Hiring Helper</div></div>
    <div class="panel">
      <p class="title" style="text-align:left;margin:10px 0 4px 6px"><span class="back">‹</span>Interview Tips</p>
      <div class="tip"><b>1</b>Start By research the Company and your Interviewers</div>
      <div class="tip"><b>2</b>Practioce Your Answers to Common Interview Qustions</div>
      <div class="tip"><b>3</b>Re-read the job description</div>
      <div class="tip"><b>4</b>Use the STAR methord in Answering Qustions</div>
      <div class="tip"><b>5</b>Recruit a Friend to Practice Answering Qustions</div>
      <div class="tip"><b>6</b>Prepare a list of References</div>
      <div class="tip"><b>7</b>Be Prepared with Examples og Our Work</div>
    </div>
    <nav class="nav"><svg class="on"><use href="#i-home"/></svg><svg><use href="#i-search"/></svg><svg><use href="#i-add"/></svg><svg><use href="#i-heart"/></svg><svg><use href="#i-user"/></svg></nav>
  </section>

  <section class="screen">
    <div class="hero"><div class="brand">Hiring Helper</div></div>
    <div class="panel">
      <div class="q-head center" style="margin-top:8px">Be Prepared with Examples og Our Work<span class="qmark">?</span><span class="arrow l">‹</span><span class="arrow r">›</span></div>
      <div class="body-card">During the Interview,you will likely be asked about Specific work you've Completed in Relation to the Position,After Reviewing the Job Description,Think of Work You've done in Past Jobs,Clubs or Volunteer Positions That Show you have Experience and Success doing the work they Require.</div>
      <div class="art" role="img" aria-label="Illustration of a person standing beside profile, heart and location icons" style="width:120px;height:64px;margin:12px 0 0 48px;background:linear-gradient(135deg,#eef2ff,#c9d6fb)"></div>
    </div>
    <nav class="nav"><svg class="on"><use href="#i-home"/></svg><svg><use href="#i-search"/></svg><svg><use href="#i-add"/></svg><svg><use href="#i-heart"/></svg><svg><use href="#i-user"/></svg></nav>
  </section>

  <section class="screen">
    <div class="hero"><div class="brand">Hiring Helper</div></div>
    <div class="panel">
      <div class="q-head center" style="margin-top:8px">Recruit a Friend to Practice Answering Questions<span class="qmark">?</span><span class="arrow l">‹</span><span class="arrow r">›</span></div>
      <div class="body-card">Actually Practicing your Answers out lound is An Incredibly effective way to prepare, Say them to Yourself or ask a Friend to Help Run Through Questions and Answers, You'll Find you gain Confidence as Get Used to Saying the Worlds.<br>Prepare a List of References Your Interviewere Might Require you to Submit a List of References</div>
      <div class="art" role="img" aria-label="Illustration of a person holding a card next to a checklist" style="width:130px;height:62px;margin:10px auto 0;background:linear-gradient(135deg,#eef2ff,#5b86f2)"></div>
    </div>
    <nav class="nav"><svg class="on"><use href="#i-home"/></svg><svg><use href="#i-search"/></svg><svg><use href="#i-add"/></svg><svg><use href="#i-heart"/></svg><svg><use href="#i-user"/></svg></nav>
  </section>

  <section class="screen dark">
    <div class="shade"></div>
    <div class="hero"><div class="brand">Hiring Helper</div></div>
    <span class="modal-x">×</span>
    <div class="modal">
      <div class="badge"><span role="img" aria-label="Gold shield award emblem"></span></div>
      <div class="modal-top">
        <h3>Lorem ipsum dolor sit</h3>
        <p>Lorem ipsum dolor sit amet, consectetur<br>adipiscing elit, sed do eiusmod tempor</p>
      </div>
      <div class="modal-body">Lorem ipsum dolor sit amet, consectetur adipiscing elit, <em>sed do eiusmod</em> tempor incididunt ut labore et dolore magna</div>
      <span class="login">Log In</span>
    </div>
    <nav class="nav"><svg class="on"><use href="#i-home"/></svg><svg><use href="#i-search"/></svg><svg><use href="#i-add"/></svg><svg><use href="#i-heart"/></svg><svg><use href="#i-user"/></svg></nav>
  </section>

</main>
</body>
</html>
```